Vantrel System Web Page Design

This project is to design 6 pages of a web based medical system for clinics, hospitals, drugs suppliers, general items suppliers, insurance company, laboratories and patients (basically all parties which could be involved in).We want the designs of the browser, button, icon and layout are based on Zeltor, which is user friendly, looks professional, simple and neat but with powerful functions. We have uploaded few pictures of another system, please do not copy its design because this is not what we are looking for, the pictures are for you to know the elements should be included in our pages. Vantrel web-base system, design 6 pages1. Login PageShould include the following elements-company id with input field-login id with input field-password with input field2. Main Page (Navigation page)Should include the following elements-Appointment-Consultation-Patient-Drugs inventory -General supplies inventory -Laboratory-Suppliers-Insurance-Reports 3. Appointment PageShould include all the the elements in the respective pictures plus the followings-Daily View, Weekly View, Monthly View buttons4. Consultation PageShould include all the the elements in the respective picture5. Patient Page5.1 General information Should include all the the elements in the respective picture5.2 medical history/lab reportsShould include all the the elements in the respective picture plus the followings-Notify patient button-Share report button.
Updated on 28 Nov:
Please stop using Harbor Suite in your designs which is not the name of our system. We have just rename our system to Vantrel, please take note.
We need the system to look professional not playful, do not use too many colors and playful icons.

```html
<!DOCTYPE html>
<html lang="en">
<head>
<meta charset="utf-8">
<title>Vantrel System (Appointment)</title>
<link href="https://fonts.googleapis.com/css2?family=Arimo:wght@400;700&display=swap" rel="stylesheet">
<style>
:root{
  --chrome-top:#e9e9e9;
  --chrome-bottom:#c9c9c9;
  --chrome-line:#9a9a9a;
  --sidebar:#e6ebf0;
  --sidebar-line:#b9c1ca;
  --sidebar-head:#6d7782;
  --icon:#6f7780;
  --select-top:#5fa6e3;
  --select-bottom:#3a84cc;
  --canvas:#e6e6e6;
  --panel:#ffffff;
  --text:#1d1d1d;
  --muted:#3a3a3a;
  --field-line:#8e8e8e;
  --table-head:#d6d6d6;
  --table-line:#cfcfcf;
  --btn:#a9a9a9;
  --btn-text:#f4f4f4;
  --btn-primary-top:#5da7e6;
  --btn-primary-bottom:#2f7fcc;
}
*{box-sizing:border-box;margin:0;padding:0}
html,body{width:1200px;height:675px;overflow:hidden;background:var(--canvas)}
body{font-family:"Arimo","Helvetica Neue",Arial,sans-serif;color:var(--text);position:relative}

.titlebar{position:absolute;left:0;top:0;width:1200px;height:51px;
  background:linear-gradient(var(--chrome-top),var(--chrome-bottom));
  border-bottom:1px solid var(--chrome-line)}
.traffic{position:absolute;top:5px;left:8px;display:flex;gap:7px}
.traffic span{width:11px;height:11px;border-radius:50%;border:1px solid rgba(0,0,0,.25)}
.traffic .close{background:#e9544b}.traffic .min{background:#e7b43c}.traffic .max{background:#5cbf47}
.nav-arrows{position:absolute;left:8px;top:23px;width:46px;height:18px;border:1px solid #8f8f8f;border-radius:4px;
  background:linear-gradient(#fbfbfb,#dcdcdc);display:flex}
.nav-arrows span{flex:1;display:flex;align-items:center;justify-content:center}
.nav-arrows span+span{border-left:1px solid #a5a5a5}
.window-title{position:absolute;top:20px;width:100%;text-align:center;font-size:11.5px;color:#333}
.search{position:absolute;right:10px;top:22px;width:168px;height:19px;border:1px solid #8d8d8d;border-radius:10px;background:#fff}
.search svg{position:absolute}

.sidebar{position:absolute;left:0;top:52px;width:166px;height:623px;background:var(--sidebar);border-right:1px solid var(--sidebar-line)}
.sidebar h2{font-size:9.5px;letter-spacing:.9px;font-weight:700;color:var(--sidebar-head);margin:28px 0 3px 9px}
.nav-item{height:21px;display:flex;align-items:center;padding-left:9px;font-size:12.5px;color:#111;gap:8px}
.nav-item svg{width:14px;height:14px;flex:none}
.nav-item.active{background:linear-gradient(var(--select-top),var(--select-bottom));color:#fff}

.search-label{position:absolute;left:208px;top:80px;font-size:11px}
.search-input{position:absolute;left:208px;top:104px;width:372px;height:28px;background:var(--panel);border-radius:2px;
  font-size:9px;color:#777;padding:10px 0 0 9px}
.patient-card{position:absolute;left:208px;top:157px;font-size:12.3px;line-height:17.6px;color:var(--muted)}
.patient-card .date{margin-top:17.6px}

.booking{position:absolute;left:703px;top:74px;width:455px;height:270px;background:var(--panel);border-radius:2px;overflow:hidden}
.field{position:absolute;font-size:10.5px}
.field .line{position:absolute;height:1px;background:var(--field-line)}
.field .chev{position:absolute}

.schedule{position:absolute;left:208px;top:372px;width:950px;border-collapse:collapse;background:var(--panel);font-size:12.5px;table-layout:fixed}
.schedule th{background:var(--table-head);height:32px;font-weight:400;font-size:11px;text-align:left;padding-left:17px;border-left:1px solid #bcbcbc}
.schedule td{height:36px;padding-left:17px;border-left:1px solid var(--table-line);border-top:1px solid var(--table-line)}
.schedule th:first-child,.schedule td:first-child{border-left:none}
.schedule .time{padding-left:18px}

.actions{position:absolute;left:208px;top:575px;width:950px;display:grid;grid-template-columns:repeat(8,102px);column-gap:19.1px;row-gap:17px}
.btn{height:27px;background:var(--btn);color:var(--btn-text);font-size:11px;display:flex;align-items:center;justify-content:center;border-radius:1px}
.btn.primary{background:linear-gradient(var(--btn-primary-top),var(--btn-primary-bottom));color:#fff}
</style>
</head>
<body>

<header class="titlebar">
  <div class="traffic"><span class="close"></span><span class="min"></span><span class="max"></span></div>
  <div class="nav-arrows">
    <span><svg width="7" height="8"><path d="M6 0L0 4l6 4z" fill="#666"/></svg></span>
    <span><svg width="7" height="8"><path d="M1 0l6 4-6 4z" fill="#666"/></svg></span>
  </div>
  <div class="window-title">Vantrel System (Appointment)</div>
  <div class="search">
    <svg style="left:6px;top:3px" width="12" height="12"><circle cx="5" cy="5" r="3.6" fill="none" stroke="#555" stroke-width="1.4"/><path d="M7.6 7.6l3.4 3.4" stroke="#555" stroke-width="1.6"/></svg>
    <svg style="right:4px;top:3px" width="11" height="11"><circle cx="5.5" cy="5.5" r="5.5" fill="#b5b5b5"/><path d="M3.5 3.5l4 4M7.5 3.5l-4 4" stroke="#fff" stroke-width="1.2"/></svg>
  </div>
</header>

<nav class="sidebar">
  <h2>IMPORTANT LINKS</h2>
  <div class="nav-item"><svg viewBox="0 0 14 14"><g fill="var(--icon)"><circle cx="3" cy="3" r="1.7"/><circle cx="7" cy="3" r="1.7"/><circle cx="11" cy="3" r="1.7"/><rect x="1.5" y="5.5" width="3" height="7"/><rect x="5.5" y="5.5" width="3" height="7"/><rect x="9.5" y="5.5" width="3" height="7"/></g></svg>Current Queue</div>
  <div class="nav-item"><svg viewBox="0 0 14 14"><rect x="1" y="2" width="12" height="11" fill="none" stroke="var(--icon)" stroke-width="1.2"/><path d="M1 5h12" stroke="var(--icon)"/><circle cx="9" cy="9.5" r="2.3" fill="none" stroke="var(--icon)"/></svg>Today Appointment</div>
  <div class="nav-item"><svg viewBox="0 0 14 14"><rect x="1" y="2" width="12" height="11" fill="none" stroke="var(--icon)" stroke-width="1.2"/><path d="M1 5h12M4 7.5h1M7 7.5h1M10 7.5h1M4 10h1M7 10h1M10 10h1" stroke="var(--icon)"/></svg>Appointment</div>
  <div class="nav-item active"><svg viewBox="0 0 14 14"><path d="M1 7c2-4 10-4 12 0-2 4-10 4-12 0z" fill="#fff"/><circle cx="7" cy="7" r="2" fill="#3a84cc"/></svg>Daily View</div>
  <div class="nav-item"><svg viewBox="0 0 14 14"><path d="M1 7c2-4 10-4 12 0-2 4-10 4-12 0z" fill="var(--icon)"/><circle cx="7" cy="7" r="2" fill="#fff"/></svg>Weekly View</div>
  <div class="nav-item"><svg viewBox="0 0 14 14"><path d="M1 7c2-4 10-4 12 0-2 4-10 4-12 0z" fill="var(--icon)"/><circle cx="7" cy="7" r="2" fill="#fff"/></svg>Monthly View</div>
  <div class="nav-item"><svg viewBox="0 0 14 14"><circle cx="7" cy="4" r="2.6" fill="none" stroke="var(--icon)" stroke-width="1.2"/><path d="M2 13c0-4 2-5.5 5-5.5s5 1.5 5 5.5z" fill="none" stroke="var(--icon)" stroke-width="1.2"/></svg>New Patient</div>
  <div class="nav-item"><svg viewBox="0 0 14 14"><path d="M2 6c1-4 9-4 10 0z" fill="var(--icon)"/><path d="M7 6v6M1 13h12" stroke="var(--icon)" stroke-width="1.2"/></svg>Public Holiday</div>
  <div class="nav-item"><svg viewBox="0 0 14 14"><path d="M3 1.5l2 2.5-1.3 1.3c.8 2 2.2 3.4 4.2 4.2L9.2 8l2.5 2-1.5 2.5C5.5 12 2 8.5 1.5 3.5z" fill="none" stroke="var(--icon)" stroke-width="1.1"/></svg>Recall</div>
  <div class="nav-item"><svg viewBox="0 0 14 14"><rect x="2" y="5" width="4" height="8" fill="none" stroke="var(--icon)" stroke-width="1.1"/><rect x="8" y="2" width="4" height="11" fill="none" stroke="var(--icon)" stroke-width="1.1"/><path d="M3 1v4" stroke="var(--icon)"/></svg>Laboratory</div>
</nav>

<div class="search-label">Patient Searching Field:</div>
<div class="search-input">Lorem Ipsum</div>

<div class="patient-card">
  <div>000001</div>
  <div>A00000(1) MALE</div>
  <div>LAM KAR WING</div>
  <div>Age: 22 Years</div>
  <div>Mob: 96543210,</div>
  <div>Tel: 23456789</div>
  <div class="date">28 June,2010</div>
</div>

<section class="booking">
  <div class="field" style="left:25px;top:42px">Patient:<span class="line" style="left:68px;top:13px;width:335px"></span></div>
  <div class="field" style="left:25px;top:68px">Date:<span class="line" style="left:68px;top:13px;width:128px"></span></div>
  <div class="field" style="left:247px;top:68px">Time:<span class="line" style="left:52px;top:13px;width:129px"></span><svg class="chev" style="left:172px;top:3px" width="8" height="5"><path d="M0 0l4 4 4-4" fill="none" stroke="#777"/></svg></div>
  <div class="field" style="left:25px;top:94px">Clinic:<span class="line" style="left:68px;top:13px;width:128px"></span><svg class="chev" style="left:187px;top:3px" width="8" height="5"><path d="M0 0l4 4 4-4" fill="none" stroke="#777"/></svg></div>
  <div class="field" style="left:247px;top:94px">Doctor:<span class="line" style="left:52px;top:13px;width:129px"></span><svg class="chev" style="left:172px;top:3px" width="8" height="5"><path d="M0 0l4 4 4-4" fill="none" stroke="#777"/></svg></div>
  <div class="field" style="left:25px;top:120px">Remarks:<span class="line" style="left:68px;top:13px;width:128px"></span><svg class="chev" style="left:187px;top:3px" width="8" height="5"><path d="M0 0l4 4 4-4" fill="none" stroke="#777"/></svg></div>
  <div class="field" style="left:247px;top:120px">Duration:<span class="line" style="left:52px;top:13px;width:129px"></span><svg class="chev" style="left:172px;top:3px" width="8" height="5"><path d="M0 0l4 4 4-4" fill="none" stroke="#777"/></svg></div>
  <div class="field" style="left:25px;top:147px">Voucher No:<span class="line" style="left:68px;top:13px;width:335px"></span></div>
  <div class="field" style="left:25px;top:173px">Memo:<span class="line" style="left:68px;top:53px;width:335px"></span></div>
</section>

<table class="schedule">
  <colgroup><col style="width:100px"><col style="width:250px"><col style="width:231px"><col style="width:92px"><col style="width:92px"><col style="width:98px"><col style="width:87px"></colgroup>
  <thead><tr><th>Patient Code</th><th>Name</th><th>Remarks</th><th>App. Time</th><th>Arr. Time</th><th>Voucher No.</th><th>Bill</th></tr></thead>
  <tbody>
    <tr><td>000001</td><td>Ho Wai Ling</td><td></td><td class="time">09:30 AM</td><td class="time">09:34 AM</td><td></td><td></td></tr>
    <tr><td>000001</td><td>Ho Wai Ling</td><td></td><td class="time">09:30 AM</td><td class="time">09:34 AM</td><td></td><td></td></tr>
    <tr><td>000001</td><td>Ho Wai Ling</td><td></td><td class="time">09:30 AM</td><td class="time">09:34 AM</td><td></td><td></td></tr>
    <tr><td>000001</td><td>Ho Wai Ling</td><td></td><td class="time">09:30 AM</td><td class="time">09:34 AM</td><td></td><td></td></tr>
  </tbody>
</table>

<div class="actions">
  <div class="btn primary">Patient</div><div class="btn">Queue</div><div class="btn">Appointment</div><div class="btn">Remarks</div>
  <div class="btn">Finish</div><div class="btn">Delete</div><div class="btn">Save Memo</div><div class="btn">Show Doctor</div>
  <div class="btn">Bill Doc.</div><div class="btn">Prescription</div><div class="btn">Document</div><div class="btn">Laboratory</div>
  <div class="btn">Glucose Data</div><div class="btn">Consultation</div><div class="btn">Print</div><div class="btn">Main</div>
</div>

</body>
</html>
```